DOUBLE SIDED BROCHURE NEEDED TO PROMOTE DOCTOR

I need a double sided DL size (99mm x 210mm) brochure, promoting a doctor seeing patients in a new area.

I want something professional. I have included the relevant information. I would also like the Dr's picture somwhere in the brochure, with a professional background. I wish to print these tomorrow, so i will pick a winner within 14 hours of posting this ad.

I have included an example of a brochures design that I recently saw, and its definietly a good starting point.

Industry/Entity Type

Medical

```html
<!DOCTYPE html>
<html lang="en">
<head>
<meta charset="utf-8">
<title>Dr. Karim Haddad – Surgical Consulting Brochure</title>
<link rel="stylesheet" href="https://fonts.googleapis.com/css2?family=Mulish:wght@700&display=swap">
<style>
  :root {
    --page-bg: #e6e6e6;
    --panel-peach: #fcccb4;
    --text-red: #d9361c;
    --orange-start: #ef8b3c;
    --orange-end: #fd6410;
    --gold: #c9b70a;
    --white: #ffffff;
    --ornament-light: #e2383c;
    --ornament-dark: #b01a20;
    --photo-sky: #8fb6e0;
    --photo-ground: #6f7d86;
  }
  * { box-sizing: border-box; margin: 0; padding: 0; }
  html, body {
    width: 1200px; height: 1200px; overflow: hidden;
    background: var(--page-bg);
    font-family: "Mulish", "Century Gothic", sans-serif;
  }
  .canvas { position: relative; width: 1200px; height: 1200px; }
  .panel {
    position: absolute; top: 101px; width: 470px; height: 997px;
    background: var(--panel-peach); overflow: hidden;
    box-shadow: 0 6px 18px rgba(0,0,0,0.25);
  }
  .panel--front { left: 100px; }
  .panel--back { left: 630px; }

  .body-copy {
    position: absolute; color: var(--text-red);
    font-weight: 700; font-size: 24px; line-height: 32px;
    white-space: nowrap;
  }
  .body-copy p + p { margin-top: 32px; }

  .ornament {
    position: absolute; border-radius: 16px;
    background: linear-gradient(135deg, var(--ornament-light), var(--ornament-dark));
    opacity: 0.85;
  }
  .panel--front .ornament { left: 262px; top: 18px; width: 165px; height: 112px; }
  .panel--back .ornament { left: 23px; top: 272px; width: 167px; height: 110px; }

  .front-letter { left: 12px; top: 103px; }

  .contact-band { position: absolute; left: 0; top: 0; width: 470px; height: 997px; }
  .contact-list {
    position: absolute; left: 14px; top: 585px;
    list-style: none; color: var(--white); font-weight: 700;
    font-size: 28px; line-height: 36px; white-space: nowrap;
  }
  .contact-item { display: flex; gap: 23px; align-items: flex-start; }
  .contact-item + .contact-item { margin-top: 36px; }
  .contact-icon { flex: 0 0 36px; width: 36px; height: 40px; margin-top: 0; }

  .hero-art { position: absolute; left: 0; top: 0; width: 470px; height: 400px; }
  .back-copy { left: 23px; top: 405px; }
  .back-copy ul { list-style: none; }
  .back-copy .group { margin-top: 13px; }
  .back-copy .group--wide { margin-top: 5px; }
</style>
</head>
<body>
<main class="canvas">

  <section class="panel panel--front" aria-label="Brochure front">
    <div class="ornament" role="img" aria-label="Decorative pair of red hearts"></div>

    <div class="body-copy front-letter">
      <p>Dear Doctors,</p>
      <p>We are pleased to announce that<br>Dr. Karim Haddad is now consulting in<br>Bayview, seeing public and<br>private patients.</p>
      <p>Guaranteed appointment within<br>two weeks, with patients having<br>the option of surgery at Coastal<br>Health Campus, Westgate Hospital or<br>St. Clare's Riverside.</p>
    </div>

    <svg class="contact-band" viewBox="0 0 470 997" aria-hidden="true">
      <defs>
        <linearGradient id="orangeBand" x1="0" y1="0" x2="1" y2="0">
          <stop offset="0" stop-color="#ef8b3c"/>
          <stop offset="1" stop-color="#fd6410"/>
        </linearGradient>
      </defs>
      <path d="M0,518 Q300,480 470,640 L470,883 Q400,970 290,997 L0,997 Z" fill="url(#orangeBand)"/>
      <path d="M0,518 Q300,480 470,640" fill="none" stroke="var(--gold)" stroke-width="6"/>
      <path d="M470,883 Q400,970 290,997" fill="none" stroke="var(--gold)" stroke-width="6"/>
    </svg>

    <ul class="contact-list">
      <li class="contact-item">
        <svg class="contact-icon" viewBox="0 0 36 40" aria-hidden="true">
          <path d="M18 2 C9 2 4 9 4 15 C4 24 18 38 18 38 C18 38 32 24 32 15 C32 9 27 2 18 2 Z" fill="#fff"/>
          <circle cx="18" cy="15" r="5" fill="#f27a2c"/>
        </svg>
        <span>Bayview Clinic:<br>42 Harbourline Road<br>Bayview WA 6199.</span>
      </li>
      <li class="contact-item">
        <svg class="contact-icon" viewBox="0 0 36 40" aria-hidden="true">
          <path d="M8 3 L14 3 L17 12 L13 16 C15 22 19 27 24 30 L28 26 L35 29 L35 36 C35 38 33 39 31 39 C16 37 4 24 3 8 C3 5 5 3 8 3 Z" fill="#fff"/>
        </svg>
        <span>Phone: 1300 555 014</span>
      </li>
      <li class="contact-item">
        <svg class="contact-icon" viewBox="0 0 36 40" aria-hidden="true">
          <rect x="10" y="4" width="18" height="14" fill="#fff"/>
          <rect x="2" y="16" width="32" height="18" rx="3" fill="#fff"/>
          <rect x="1" y="17" width="6" height="17" rx="2" fill="#f27a2c" stroke="#fff" stroke-width="2"/>
          <rect x="12" y="22" width="16" height="2" fill="#f27a2c"/>
          <rect x="12" y="27" width="16" height="2" fill="#f27a2c"/>
        </svg>
        <span>Please send all referrals by<br>fax to (08) 5550 1427.</span>
      </li>
    </ul>
  </section>

  <section class="panel panel--back" aria-label="Brochure back">
    <svg class="hero-art" viewBox="0 0 470 400" role="img" aria-label="Portrait of the surgeon in front of the hospital building">
      <defs>
        <linearGradient id="heroPhoto" x1="0" y1="0" x2="0" y2="1">
          <stop offset="0" stop-color="var(--photo-sky)"/>
          <stop offset="1" stop-color="var(--photo-ground)"/>
        </linearGradient>
      </defs>
      <path d="M0,118 Q120,12 310,0 L470,0 L470,355 Q250,362 0,292 Z" fill="url(#heroPhoto)"/>
      <path d="M0,118 Q120,12 310,0" fill="none" stroke="var(--gold)" stroke-width="7"/>
      <path d="M0,292 Q250,362 470,355" fill="none" stroke="var(--gold)" stroke-width="7"/>
    </svg>
    <div class="ornament" role="img" aria-label="Decorative pair of red hearts"></div>

    <div class="body-copy back-copy">
      <p>Dr. Haddad is a highly trained<br>specialised surgeon, in all areas<br>of Endocrine, Breast and General<br>Surgery. Including:</p>
      <ul class="group">
        <li>•Thyroid Surgery</li>
        <li>• Parathyroid surgery (including</li>
        <li>minimally invasive</li>
        <li>parathyroidectomy)</li>
        <li>• Breast Cancer Benign breast</li>
        <li>lesions</li>
      </ul>
      <p class="group group--wide">All areas of general surgery,<br>such as;</p>
      <ul class="group group--wide">
        <li>•Gallbladder surgery</li>
        <li>•Hernia surgery</li>
        <li>•Haemorrhoids</li>
        <li>•Carpal Tunnel</li>
        <li>•Vasectomy etc etc…</li>
      </ul>
    </div>
  </section>

</main>
</body>
</html>
```